Brevard Trade Partners - we are Asian sourcing agents

We are sourcing agents based in the USA and we act as sourcing agents for clients in throughout the world. We focus primarily on custom sewn goods. So basically companies who do not have the in-house expertise to do it themselves, come to us and have us find suitable factories in Asia to do the production. We are middlemen. We find the factories...quote the project...manage the quality control and then deliver the goods directly to our customer's door. We pride ourselves in making the communication very easy and precise.

Current page is www.brevardtradepartners.com

I am not happy w/ the overall look. The spacing...the photos, the fonts...the design elements...the pictures. I want a cool, crisp design that conveys professionalism and clearly depicts/explains what we do.

Requirements
Must have
• use my logo....I like it...it was designed by someone on this website.
Nice to have
• a video/animation of the entire process would be wonderful. Showing initial contact with our office in the USA...then to my correspondence with my offices in Taiwan and in Hong Kong...and then back and fort w/ the customer.....and then between my people in Hong Kong/Taiwan with the local factories......and then a quote is generated and sent to my client......to samples being made and sent for approval.....to a PO being generated......to final samples being sent.....to the order being shipped and delivered to the clients warehouse. I was thinking of an animation showing arrows and text showing the back and forth communication and explaining how the process flows.

```html
<!DOCTYPE html>
<html lang="en">
<head>
<meta charset="utf-8">
<title>Brevard Trade Partners – Asian Outsourcing Made Easy</title>
<link rel="stylesheet" href="https://fonts.googleapis.com/css2?family=Open+Sans:ital,wght@0,400;0,600;0,700;1,600&family=Arimo:wght@400;700&display=swap">
<style>
:root{
  --navy:#0e1248;
  --ink:#222;
  --text:#444;
  --muted:#555;
  --accent:#6a8c1a;
  --services-bg:#f4f5fb;
  --links-bg:#dcdcdc;
  --card-line:#e2e2e8;
  --white:#fff;
}
*{margin:0;padding:0;box-sizing:border-box}
html,body{width:1200px;height:2261px;overflow:hidden}
body{position:relative;background:var(--white);font-family:"Open Sans",Arial,sans-serif;color:var(--text)}
.abs{position:absolute}

/* Hero */
.hero{left:0;top:0;width:1200px;height:630px;background:linear-gradient(180deg,#5d7fa8 0%,#9aa6b8 28%,#7b6f6b 45%,#5a5450 62%,#8e8a86 80%,#6f6b68 100%)}
.hero-shade{left:0;top:0;width:1200px;height:630px;background:linear-gradient(90deg,rgba(0,0,0,0) 40%,rgba(0,0,0,.18) 100%)}
.site-nav{left:100px;top:48px;width:1001px;height:85px;background:var(--white);border-top:5px solid var(--navy);box-shadow:0 3px 8px rgba(0,0,0,.25)}
.brand{left:32px;top:18px;font-weight:700;font-size:21px;line-height:26px;color:var(--navy);letter-spacing:.5px}
.brand small{display:block;font-size:21px}
.menu{left:405px;top:0;height:80px;display:flex;list-style:none}
.menu li{font-size:13px;font-weight:600;color:#333;text-transform:uppercase;padding:0 22px;line-height:60px}
.menu li.active{background:var(--navy);color:var(--white);padding:0 11px;margin-right:22px;height:60px}
.search-icon{left:952px;top:18px}
.hero-title{right:99px;top:326px;font-size:37px;font-weight:700;color:var(--white);text-shadow:0 2px 4px rgba(0,0,0,.5);text-align:right;white-space:nowrap}
.hero-sub{right:99px;top:384px;font-size:23px;font-weight:600;font-style:italic;color:var(--white);text-shadow:0 2px 3px rgba(0,0,0,.5);white-space:nowrap}
.hero-btn{left:909px;top:446px;width:192px;height:47px;background:var(--navy);border:2px solid var(--white);color:var(--white);font-size:14px;font-weight:700;display:flex;align-items:center;justify-content:center;gap:14px}
.slide-arrow{top:298px}

/* Intro */
.intro-photo{left:119px;top:676px;width:184px;height:161px;background:linear-gradient(180deg,#8c3a30 0%,#6d4a45 45%,#2a2a2e 100%)}
.intro-title{left:351px;top:678px;font-size:23px;font-weight:600;color:var(--ink);white-space:nowrap}
.intro-text{left:354px;top:722px;font-size:14.5px;color:var(--muted);white-space:nowrap}
.btn{background:var(--navy);color:var(--white);font-weight:700;display:flex;align-items:center;justify-content:center;gap:14px}
.intro-btn{left:356px;top:777px;width:188px;height:45px;font-size:14px}

/* Services */
.services{left:0;top:887px;width:1200px;height:490px;background:var(--services-bg);border-top:1px solid #e3e4ee;border-bottom:1px solid #e3e4ee}
.section-title{font-size:35px;font-weight:600;color:var(--ink);white-space:nowrap}
.svc-title{left:101px;top:915px}
.svc-kicker{left:105px;top:990px;font-size:14px;font-weight:700;color:var(--muted);white-space:nowrap}
.svc-copy{left:101px;top:1033px;width:775px;font-family:Arimo,Arial,sans-serif;font-size:13px;line-height:26px;color:var(--muted)}
.service-card{top:1137px;width:217px;height:202px;background:var(--white);border:1px solid var(--card-line)}
.service-card .thumb{position:absolute;left:6px;top:6px;width:203px;height:148px;border:1px solid #ececec}
.service-card .label{position:absolute;left:0;right:0;top:167px;text-align:center;font-size:14px;font-weight:600;color:#222}

/* How it works */
.how-title{left:101px;top:1432px}
.how-copy{left:100px;top:1496px;width:545px;font-family:Arimo,Arial,sans-serif;font-size:12.8px;line-height:25.6px;color:#333}
.how-btn{left:100px;top:1719px;width:122px;height:45px;font-family:Arimo,Arial,sans-serif;font-size:13.5px;box-shadow:0 2px 3px rgba(0,0,0,.35)}
.video{left:680px;top:1457px;width:422px;height:310px;background:linear-gradient(180deg,#9aa0a8 0%,#4d5058 40%,#3a2c38 70%,#1d1d22 100%);border:1px solid #888}
.video-bar{left:0;bottom:0;width:420px;height:34px;background:linear-gradient(180deg,rgba(0,0,0,0),rgba(0,0,0,.55))}

/* Footer links */
.link-band{left:0;top:1811px;width:1200px;height:254px;background:var(--links-bg)}
.link-col{top:1847px;width:200px}
.link-col h3{font-size:17.5px;font-weight:600;color:#333;line-height:21px;margin-bottom:14px}
.link-col ul{list-style:none}
.link-col li{font-size:12.5px;color:#444;line-height:15px;margin-bottom:10.5px}

/* Bottom bar */
.site-footer{left:0;top:2065px;width:1200px;height:196px;background:var(--navy)}
.contact{left:100px;color:var(--white);font-size:13.5px;line-height:21px;display:flex;gap:10px;align-items:flex-start;white-space:nowrap}
.social{left:975px;display:flex;gap:11px}
.social span{width:16px;height:16px;border-radius:50%;background:var(--white)}
.copyright{right:99px;color:var(--white);font-size:13px;font-weight:600;white-space:nowrap}
</style>
</head>
<body>

<header>
  <div class="abs hero" role="img" aria-label="Photograph of an ancient Chinese city wall walkway lined with red lanterns and flags under an evening sky"></div>
  <div class="abs hero-shade"></div>

  <nav class="abs site-nav">
    <div class="abs brand">BREVARD<small>TRADE PARTNERS</small></div>
    <ul class="abs menu">
      <li class="active">Home</li>
      <li>Product Categories</li>
      <li>About Us</li>
      <li>Request Quote</li>
    </ul>
    <svg class="abs search-icon" width="22" height="22" viewBox="0 0 22 22" aria-label="Search"><circle cx="9" cy="9" r="6" fill="none" stroke="#6a8c1a" stroke-width="3"/><line x1="13.5" y1="13.5" x2="19" y2="19" stroke="#6a8c1a" stroke-width="3.5" stroke-linecap="round"/></svg>
  </nav>

  <svg class="abs slide-arrow" style="left:24px" width="36" height="36" viewBox="0 0 36 36" aria-label="Previous slide"><circle cx="18" cy="18" r="16" fill="rgba(0,0,0,.25)" stroke="#fff" stroke-width="2.5"/><path d="M21 10 L13 18 L21 26 Z" fill="#fff"/></svg>
  <svg class="abs slide-arrow" style="left:1136px" width="36" height="36" viewBox="0 0 36 36" aria-label="Next slide"><circle cx="18" cy="18" r="16" fill="rgba(0,0,0,.25)" stroke="#fff" stroke-width="2.5"/><path d="M15 10 L23 18 L15 26 Z" fill="#fff"/></svg>

  <h1 class="abs hero-title">ASIAN OUTSOURCING MADE EASY!</h1>
  <p class="abs hero-sub">Custom Sewn Goods Made to Your Specifications</p>
  <div class="abs hero-btn">REQUEST A QUOTE <span>&raquo;</span></div>
</header>

<main>
  <section>
    <div class="abs intro-photo" role="img" aria-label="Portrait of the company founder standing in front of a historic Chinese gate"></div>
    <h2 class="abs intro-title">Outsource Your Sewing Needs to Trusted Contractors in China</h2>
    <p class="abs intro-text">Please contact us for immediate consultation regarding your outsourcing project.</p>
    <div class="abs btn intro-btn">REQUEST A QUOTE <span>&raquo;</span></div>
  </section>

  <div class="abs services"></div>
  <section>
    <h2 class="abs section-title svc-title">OUR SERVICES</h2>
    <p class="abs svc-kicker">NEQUE PORRO QUISQUAM EST QUI DOLOREM IPSUM QUIA DOLOR SIT AMET.</p>
    <p class="abs svc-copy">Lorem Ipsum is simply dummy text of the printing and typesetting industry. Lorem Ipsum has been the industry's standard<br>dummy text ever since the 1500s, when an unknown printer took a galley of type and scrambled it to make a type specimen book.<br>It has survived not only five centuries.</p>

    <div class="abs service-card" style="left:101px">
      <div class="thumb" role="img" aria-label="Black messenger bag with red and grey stripes" style="background:radial-gradient(ellipse at 50% 50%,#3a2a2c 0%,#222 40%,#fff 70%)"></div>
      <div class="label">BAGS</div>
    </div>
    <div class="abs service-card" style="left:363px">
      <div class="thumb" role="img" aria-label="Red, black and white golf bags" style="background:radial-gradient(ellipse at 50% 55%,#b8242c 0%,#4a2a2e 40%,#fff 72%)"></div>
      <div class="label">SPORTING GOODS</div>
    </div>
    <div class="abs service-card" style="left:624px">
      <div class="thumb" role="img" aria-label="Row of colourful phone cases" style="background:linear-gradient(90deg,#fff 5%,#222 12%,#2a2f8a 25%,#6a2c8c 40%,#c0208a 55%,#d8202a 70%,#e8a020 85%,#fff 93%)"></div>
      <div class="label">CASES</div>
    </div>
    <div class="abs service-card" style="left:886px">
      <div class="thumb" role="img" aria-label="Navy and silver motorcycle cover" style="background:radial-gradient(ellipse at 50% 55%,#20286a 0%,#4a5290 35%,#fff 70%)"></div>
      <div class="label">COVERS</div>
    </div>
  </section>

  <section>
    <h2 class="abs section-title how-title">HOW IT WORKS</h2>
    <p class="abs how-copy">Brevard Trade Partners has been sourcing custom sewn goods in Asia since 1998. We work with our clients by matching their unique production needs with the best possible China sewing factories. We manage the entire process from start to finish, by first identifying the best factories to quote each job. The next step is negotiating the best (fair) price possible. We complete the process by monitoring the quality of the goods during production, and then managing the ocean logistics, customs clearances and local delivery right to your door. Our services and our total commitment to customer satisfaction help level the playing field by giving our customers access to low cost, high quality China contract sewing.</p>
    <div class="abs btn how-btn">READ MORE</div>

    <div class="abs video" role="img" aria-label="Video of workers at sewing machines in a garment factory">
      <svg class="abs" style="left:180px;top:133px" width="50" height="50" viewBox="0 0 50 50"><circle cx="25" cy="25" r="23" fill="rgba(0,0,0,.45)" stroke="#fff" stroke-width="3"/><path d="M19 14 L36 25 L19 36 Z" fill="#fff"/></svg>
      <div class="abs video-bar"></div>
      <svg class="abs" style="left:30px;top:280px" width="370" height="16" viewBox="0 0 370 16">
        <path d="M0 3 L8 8 L0 13 Z" fill="#fff"/>
        <rect x="14" y="3" width="3" height="10" fill="#fff"/><rect x="19" y="3" width="3" height="10" fill="#fff"/>
        <rect x="28" y="3" width="10" height="10" fill="#fff"/>
        <rect x="50" y="7" width="155" height="2" fill="#ddd"/><rect x="50" y="7" width="36" height="2" fill="#8ab020"/>
        <text x="220" y="12" fill="#fff" font-family="Arimo, Arial, sans-serif" font-size="9">1:08/12:06</text>
        <path d="M278 6 h3 l4 -3 v10 l-4 -3 h-3 Z" fill="#fff"/>
        <rect x="303" y="10" width="2" height="3" fill="#fff"/><rect x="306" y="8" width="2" height="5" fill="#fff"/><rect x="309" y="6" width="2" height="7" fill="#fff"/><rect x="312" y="4" width="2" height="9" fill="#fff"/>
        <rect x="328" y="3" width="12" height="10" fill="#fff"/>
      </svg>
    </div>
  </section>
</main>

<div class="abs link-band"></div>
<nav aria-label="Product categories">
  <div class="abs link-col" style="left:100px">
    <h3>Custom Cases</h3>
    <ul><li>Cosmetic Cases</li><li>Phone Cases</li><li>Tool Bags and Tool Cases</li></ul>
  </div>
  <div class="abs link-col" style="left:311px">
    <h3>Custom Gloves</h3>
    <ul><li>Batting Gloves</li><li>Garden Gloves</li><li>Mechanic Gloves</li><li>Ski Gloves</li></ul>
  </div>
  <div class="abs link-col" style="left:490px;width:200px">
    <h3 style="white-space:nowrap">Custom Sewn Goods</h3>
    <ul><li style="width:145px">Pet Collars, Leashes, &amp; Harnesses</li><li>Socks</li></ul>
  </div>
  <div class="abs link-col" style="left:713px;width:180px">
    <h3 style="width:140px">Custom Sporting Goods</h3>
    <ul><li>Yoga Mats</li><li style="white-space:nowrap">Yoga Gear and Accessories</li></ul>
  </div>
  <div class="abs link-col" style="left:927px;width:180px">
    <h3>Custom Medical Accessories</h3>
    <ul><li style="white-space:nowrap">Medical Equipment Covers</li><li>Medical Pads</li><li style="width:160px">Medical Sheets &amp; Bedding Supplies</li><li style="white-space:nowrap">Oxygen Tank Cases and Bags</li></ul>
  </div>
</nav>

<footer class="abs site-footer">
  <div class="abs contact" style="top:25px;left:100px">
    <svg width="11" height="15" viewBox="0 0 11 15" style="margin-top:3px"><path d="M5.5 0 C2.5 0 0 2.4 0 5.4 C0 9.5 5.5 15 5.5 15 C5.5 15 11 9.5 11 5.4 C11 2.4 8.5 0 5.5 0 Z" fill="#fff"/><circle cx="5.5" cy="5.4" r="2" fill="#0e1248"/></svg>
    <span>Brevard Trade Partners, LLC Four Harbor Lane<br><span style="margin-left:-21px">Suite B-2</span><br><span style="margin-left:-21px">Melbourne, FL 32901</span></span>
  </div>
  <div class="abs contact" style="top:101px">
    <svg width="13" height="13" viewBox="0 0 13 13" style="margin-top:4px"><path d="M2.5 0.5 L5 3 L3.5 5 C4.5 7 6 8.5 8 9.5 L10 8 L12.5 10.5 L11 12.5 C5 12 1 8 0.5 2 Z" fill="#fff"/></svg>
    <span>Tel: 321-555-0148</span>
  </div>
  <div class="abs contact" style="top:128px">
    <svg width="14" height="14" viewBox="0 0 14 14" style="margin-top:3px"><rect x="3" y="0" width="8" height="4" fill="#fff"/><rect x="0" y="5" width="14" height="9" rx="1" fill="#fff"/><rect x="3" y="8" width="8" height="1.5" fill="#0e1248"/></svg>
    <span>Fax: 321-555-0172</span>
  </div>
  <div class="abs contact" style="top:155px">
    <svg width="15" height="11" viewBox="0 0 15 11" style="margin-top:5px"><rect width="15" height="11" rx="1" fill="#fff"/><path d="M0.5 1 L7.5 6.5 L14.5 1" fill="none" stroke="#0e1248" stroke-width="1.3"/></svg>
    <span>Email: info@brevardtradepartners.com</span>
  </div>
  <div class="abs social" style="top:107px" aria-label="Social media links"><span></span><span></span><span></span><span></span></div>
  <p class="abs copyright" style="top:138px">© Brevard Trade Partners. All rights are reseved.</p>
</footer>

</body>
</html>
```